BRIGHT RIVER POWER.

I'd like my business logo.
contact name: Dennis Halvorsen
phone:0438759164
email: info@brightriverpower.net.au
website: www.brightriverpower.net.au

services:
solar
battery storage
LED lighting
energy saving solutions
general electrical
I'd like the design to look professional

Target Market(s)

Everyone

Industry/Entity Type

Business

Contact Information for Business Card

as described above

Requirements
Must have
• Id like the colours and the design to work well with my logo.

```html
<!DOCTYPE html>
<html lang="en">
<head>
<meta charset="utf-8">
<title>Bright River Power – Business Card</title>
<link rel="stylesheet" href="https://fonts.googleapis.com/css2?family=Open+Sans:wght@400;600&display=swap">
<style>
  :root {
    --page-bg: #ededed;
    --card-white: #ffffff;
    --brand-green: #4c9f33;
    --brand-orange: #f6a21c;
    --text-grey: #444444;
    --divider: #c8c8c8;
    --green-light: #93c83e;
    --green-dark: #43a035;
    --white: #ffffff;
  }
  * { margin: 0; padding: 0; box-sizing: border-box; }
  html, body {
    width: 1105px;
    height: 1200px;
    overflow: hidden;
    background: var(--page-bg);
    font-family: "Open Sans", sans-serif;
  }
  .card {
    position: absolute;
    left: 193px;
    width: 720px;
    height: 410px;
  }
  .card-front {
    top: 167px;
    background: var(--card-white);
  }
  .card-back {
    top: 623px;
    background: radial-gradient(ellipse at 50% 45%, var(--green-light) 0%, var(--green-dark) 75%);
  }
  .brand-mark {
    position: absolute;
    left: 58px;
    top: 158px;
    display: flex;
    align-items: center;
    gap: 10px;
  }
  .brand-dot {
    width: 22px;
    height: 22px;
    border-radius: 50%;
    background: var(--brand-orange);
  }
  .brand-name {
    font-weight: 600;
    font-size: 27px;
    color: var(--brand-green);
    white-space: nowrap;
  }
  .divider {
    position: absolute;
    left: 365px;
    top: 134px;
    width: 1px;
    height: 138px;
    background: var(--divider);
  }
  .contact {
    position: absolute;
    left: 388px;
    top: 138px;
  }
  .contact-name {
    font-weight: 600;
    font-size: 26px;
    color: var(--brand-green);
    margin-bottom: 10px;
  }
  .contact-list { list-style: none; }
  .contact-item {
    display: flex;
    align-items: center;
    gap: 9px;
    font-size: 19px;
    line-height: 28px;
    color: var(--text-grey);
  }
  .contact-icon { width: 17px; height: 17px; flex: none; }
  .back-brand {
    position: absolute;
    left: 0;
    right: 0;
    top: 150px;
    display: flex;
    justify-content: center;
    align-items: center;
    gap: 12px;
  }
  .back-brand .brand-dot { background: var(--white); width: 26px; height: 26px; }
  .back-brand .brand-name { color: var(--white); font-size: 38px; }
  .services {
    position: absolute;
    left: 0;
    right: 0;
    top: 322px;
    text-align: center;
    color: var(--white);
    font-size: 20px;
    line-height: 28px;
  }
</style>
</head>
<body>
  <section class="card card-front">
    <div class="brand-mark">
      <span class="brand-dot"></span>
      <span class="brand-name">Bright River Power</span>
    </div>
    <div class="divider"></div>
    <div class="contact">
      <p class="contact-name">Dennis Halvorsen</p>
      <ul class="contact-list">
        <li class="contact-item">
          <svg class="contact-icon" viewBox="0 0 24 24" aria-hidden="true"><path fill="#4c9f33" d="M6.6 10.8a15.1 15.1 0 0 0 6.6 6.6l2.2-2.2c.3-.3.7-.4 1-.2 1.1.4 2.3.6 3.6.6.6 0 1 .4 1 1V20c0 .6-.4 1-1 1A17 17 0 0 1 3 4c0-.6.4-1 1-1h3.5c.6 0 1 .4 1 1 0 1.3.2 2.5.6 3.6.1.3 0 .7-.2 1z"/></svg>
          <span>0438759164</span>
        </li>
        <li class="contact-item">
          <svg class="contact-icon" viewBox="0 0 24 24" aria-hidden="true"><rect x="2" y="5" width="20" height="14" fill="#4c9f33"/><path d="M2 5l10 8 10-8" fill="none" stroke="#ffffff" stroke-width="2"/></svg>
          <span>info@brightriverpower.net.au</span>
        </li>
        <li class="contact-item">
          <svg class="contact-icon" viewBox="0 0 24 24" aria-hidden="true"><circle cx="12" cy="12" r="10" fill="#4c9f33"/><path d="M7 8c2 0 3 1 3 3s-2 2-2 4M15 5c-1 2 1 3 2 4s0 3 1 4" fill="none" stroke="#ffffff" stroke-width="1.8"/></svg>
          <span>brightriverpower.net.au</span>
        </li>
      </ul>
    </div>
  </section>

  <section class="card card-back">
    <div class="back-brand">
      <span class="brand-dot"></span>
      <span class="brand-name">Bright River Power</span>
    </div>
    <p class="services">Solar &bull; Battery storage &bull; LED lighting<br>Energy saving solutions</p>
  </section>
</body>
</html>
```